Distribution company for alcoholic beverages called Amber Crestline needs a web design

1. We would like to first page to show

A. The company logo (in att)

B. A wall of bottles similar to
- www.underpaperskies.com that will click through to the brand info
- https://keltaronworks.com/brands/
PLEASE NOTE THAT IT CAN NOT BE THE SAME DESIGN - it needs to have a different look and feel ... this is to show what we mean with a wall of bottles

Important = we need to be able to keep adding new bottles/brands over time

C. only 3 tabs needed – Brands, About Us and Contact

Style
- simple and clean
- colourful
- classy

2. Page 2
The intro page to describe the company
we can use the same (Box + drop) logo to create a visual

3. Page 3
The referral page to the specific brands/company
= we need to alternating versions of this / just different ordering in the page

Target Market(s)

importers, brand owners, bartenders,

Industry/Entity Type

It Company

Number of Pages Required

3 page

Requirements
Must have
• A landing page visual that can display bottles we will sell in an organised way
• We need to be able to add bottles when the portfolio expands
Nice to have
• to have the drop out of the logo as a part of the design of the website

```html
<!DOCTYPE html>
<html lang="en">
<head>
<meta charset="utf-8">
<title>Amber Crestline – About Us</title>
<link href="https://fonts.googleapis.com/css2?family=Roboto:wght@400;500&display=swap" rel="stylesheet">
<style>
  :root {
    --ink: #111111;
    --white: #ffffff;
    --frame: #e5e5e5;
    --night: #000000;
    --ember-dark: #1a0802;
    --ember-mid: #7a2a08;
    --ember-bright: #f0a020;
  }
  * { box-sizing: border-box; margin: 0; padding: 0; }
  html, body { width: 1035px; height: 1200px; overflow: hidden; }
  body {
    position: relative;
    background: var(--white);
    font-family: "Roboto", Arial, sans-serif;
    color: var(--ink);
  }
  .hero {
    position: absolute; left: 0; top: 0; width: 1035px; height: 485px;
    background:
      radial-gradient(ellipse 45% 40% at 45% 12%, var(--ember-bright) 0%, rgba(240,160,32,0.5) 45%, rgba(240,160,32,0) 100%),
      linear-gradient(180deg, #9a3a0a 0%, var(--ember-mid) 45%, #3a1204 80%, var(--ember-dark) 100%);
  }
  .site-header, .site-footer .bar {
    position: absolute; left: 184px; width: 652px;
    display: flex; align-items: center; justify-content: space-between;
  }
  .site-header { top: 28px; height: 41px; }
  .brand-name {
    font-weight: 500; font-size: 15px; letter-spacing: 1.5px;
    color: var(--white); text-transform: uppercase; white-space: nowrap;
  }
  .site-footer .brand-name { font-size: 11px; letter-spacing: 1px; }
  .main-nav { display: flex; align-items: center; }
  .main-nav a {
    display: block; width: 75px; height: 24px; line-height: 22px;
    margin-left: 15px; text-align: center;
    font-size: 9px; font-weight: 500; letter-spacing: 0.3px;
    color: var(--white); text-decoration: none; text-transform: uppercase;
    border: 1px solid transparent;
  }
  .main-nav a.is-current { border-color: var(--white); }
  .about-frame {
    position: absolute; left: 262px; top: 580px; width: 510px; height: 460px;
    border: 13px solid var(--frame);
  }
  .about-copy {
    position: absolute; left: 297px; top: 654px; width: 445px;
    font-size: 10.5px; line-height: 19px; letter-spacing: 0.55px;
  }
  .about-cta {
    position: absolute; left: 297px; top: 885px; width: 440px; text-align: center;
    font-size: 13px; line-height: 19px; letter-spacing: 0.8px;
  }
  .about-cta p + p { margin-top: 16px; }
  .site-footer {
    position: absolute; left: 0; top: 1118px; width: 1035px; height: 82px;
    background: var(--night);
  }
  .site-footer .bar { top: 28px; height: 26px; }
</style>
</head>
<body>
  <div class="hero" role="img" aria-label="Photograph of oak barrels in a row being charred, with tall flames rising from their open tops in a dark cooperage"></div>

  <header class="site-header">
    <div class="brand-name">Amber Crestline</div>
    <nav class="main-nav">
      <a href="#">Home</a>
      <a href="#">Brands</a>
      <a href="#" class="is-current">About Us</a>
      <a href="#">Contact</a>
    </nav>
  </header>

  <div class="about-frame"></div>

  <div class="about-copy">
    <p>Amber Crestline started with one thought: “Wouldn’t it be amazing if smaller local authentic brands could find a way to have a global outreach?”.</p>
    <p>As more craft brands enter the market place, we’ve noticed many of them could use a hand when it comes to creating and executing an export strategy. Understanding legislation, international pricing and finding the right distribution partner are just a few of the challenges they face.</p>
    <p>We offer vast export expertise from actively working in over 90 markets. Our support could consist of setting up your international export network. We are also able to provide more continuous support in your export markets by putting together marketing plans and activation visits by our own brand ambassador team.</p>
  </div>

  <div class="about-cta">
    <p>If you are interested to learn more feel free to contact us for a initial conversation.</p>
    <p>Let us prove (y)our strength!</p>
  </div>

  <footer class="site-footer">
    <div class="bar">
      <div class="brand-name">Amber Crestline</div>
      <nav class="main-nav">
        <a href="#">Home</a>
        <a href="#">Brands</a>
        <a href="#" class="is-current">About Us</a>
        <a href="#">Contact</a>
      </nav>
    </div>
  </footer>
</body>
</html>
```